High Tech Real Estate Startup needs a business card

We are developing an innovative real estate marketing product based around advanced search and virtual reality.

We talk to people, we need business cards.

Target Market(s)

The target market is technology professionals and realtors.

Contact Information for Business Card

The information to be included will include

Name
Title
Phone Number
E-mail Address
www.zelquin.com

It should use simple iconography for each one of those fields.

Font styles to use
Other font styles liked:
• Co, Jubilat, Avenir

Colors

Designer to choose colors to be used in the design.

Requirements
Must have
• Clean aesthetic,
• Good use of negative space.
• It should use our company logo, shown in the attached file. It is able to use the negative of that logo (coloured font and white background) and I have attached other acceptable accent colours in a swatch file.
Should not have
• Should not be too busy
• No extraneous text (slogans, tag lines etc)

```html
<!DOCTYPE html>
<html lang="en">
<head>
<meta charset="utf-8">
<title>Zelquin Business Card</title>
<link rel="stylesheet" href="https://fonts.googleapis.com/css2?family=Open+Sans:wght@400;600&display=swap">
<style>
  :root {
    --backdrop: #3b3b3d;
    --card: #1e1e20;
    --accent: #3fbdbd;
    --text-light: #e6e6e6;
    --icon-fill: #1e1e20;
  }
  * { margin: 0; padding: 0; box-sizing: border-box; }
  html, body {
    width: 799px;
    height: 1200px;
    overflow: hidden;
    background: var(--backdrop);
    font-family: "Open Sans", Arial, sans-serif;
  }
  .sheet {
    position: relative;
    width: 799px;
    height: 1200px;
  }
  .card {
    position: absolute;
    left: 90px;
    width: 620px;
    height: 354px;
    background: var(--card);
    border-radius: 28px;
    overflow: hidden;
  }
  .card-front { top: 120px; }
  .card-back {
    top: 720px;
    border-bottom: 6px solid var(--accent);
  }
  .wordmark {
    color: var(--accent);
    font-weight: 600;
    letter-spacing: 4px;
    line-height: 1;
    white-space: nowrap;
  }
  .card-front .wordmark {
    position: absolute;
    left: 0; right: 0;
    top: 142px;
    text-align: center;
    font-size: 64px;
  }
  .card-back .wordmark {
    position: absolute;
    right: 60px;
    top: 214px;
    font-size: 46px;
  }
  .identity {
    position: absolute;
    left: 44px;
    top: 44px;
  }
  .person-name {
    color: var(--accent);
    font-weight: 600;
    font-size: 25px;
    line-height: 1.15;
  }
  .person-title {
    color: var(--text-light);
    font-size: 13px;
    margin-top: 2px;
  }
  .contact-list {
    position: absolute;
    left: 44px;
    top: 188px;
    list-style: none;
  }
  .contact-item {
    display: flex;
    align-items: center;
    gap: 10px;
    color: var(--text-light);
    font-size: 14px;
    line-height: 1;
    margin-bottom: 9px;
    white-space: nowrap;
  }
  .contact-icon {
    width: 16px;
    height: 16px;
    flex: none;
  }
</style>
</head>
<body>
<main class="sheet">
  <section class="card card-front">
    <div class="wordmark">ZELQUIN</div>
  </section>

  <section class="card card-back">
    <div class="identity">
      <h1 class="person-name">Alex Rowe Parker</h1>
      <p class="person-title">Managing Director</p>
    </div>

    <ul class="contact-list">
      <li class="contact-item">
        <svg class="contact-icon" viewBox="0 0 16 16" aria-hidden="true">
          <circle cx="8" cy="8" r="8" fill="var(--accent)"/>
          <path d="M5.3 4.2l1.4 1.6-.7 1.1c.5 1.1 1.3 1.9 2.4 2.4l1.1-.7 1.6 1.4-.8 1.3c-2.8-.3-5.3-2.8-5.6-5.6z" fill="var(--icon-fill)"/>
        </svg>
        <span>555.014.2837</span>
      </li>
      <li class="contact-item">
        <svg class="contact-icon" viewBox="0 0 16 16" aria-hidden="true">
          <circle cx="8" cy="8" r="8" fill="var(--accent)"/>
          <rect x="4" y="5.2" width="8" height="5.6" rx="0.6" fill="var(--icon-fill)"/>
          <path d="M4.3 5.6L8 8.4l3.7-2.8" stroke="var(--accent)" stroke-width="0.8" fill="none"/>
        </svg>
        <span>alexrowe@zelquin.com</span>
      </li>
      <li class="contact-item">
        <svg class="contact-icon" viewBox="0 0 16 16" aria-hidden="true">
          <circle cx="8" cy="8" r="8" fill="var(--accent)"/>
          <circle cx="8" cy="8" r="4.2" fill="none" stroke="var(--icon-fill)" stroke-width="1"/>
          <ellipse cx="8" cy="8" rx="1.8" ry="4.2" fill="none" stroke="var(--icon-fill)" stroke-width="0.9"/>
          <path d="M3.8 8h8.4" stroke="var(--icon-fill)" stroke-width="0.9"/>
        </svg>
        <span>www.zelquin.com</span>
      </li>
    </ul>

    <div class="wordmark">ZELQUIN</div>
  </section>
</main>
</body>
</html>
```